Animal Eye Clinic needs a Business card

We are a new veterinary ophthalmology practice (Ridgeline Pet Vision Care) and we need a business card designed. We only see animal eyes - we are not a regular veterinary clinic. We already have a logo. We are looking for a professional, good looking business card to hand out to our clients. We are looking for something simple but professional and contemporary. Our logo is likely the only picture/graphic that needs to be on the card.
Updates

Contact Information for Business Card

Delia Vossman, BSc, DVM, MSc, DipACVO
Veterinary Ophthalmologist

Phone: 250.418.3927
Email: ridgelinepetvisioncare@mailbox-example.net
Website: ridgelinepetvisioncare-example.net
Address: 1874 Thornbury Rd
Kelowna, BC, V1X 4M9

Colors

Designer to choose colors to be used in the design.

Requirements
Must have
• Our logo (attached)

```html
<!DOCTYPE html>
<html lang="en">
<head>
<meta charset="utf-8">
<title>Ridgeline Pet Vision Care – Business Card</title>
<link rel="stylesheet" href="https://fonts.googleapis.com/css2?family=Open+Sans:wght@400;700&display=swap">
<style>
  :root {
    --teal: #1b95a3;
    --teal-dark: #17808c;
    --ink: #6b6b6b;
    --paper: #ffffff;
    --backdrop: #e4e6e8;
  }
  * { box-sizing: border-box; margin: 0; padding: 0; }
  html, body { width: 1200px; height: 800px; overflow: hidden; }
  body {
    background: var(--backdrop);
    font-family: "Open Sans", Arial, sans-serif;
    position: relative;
  }
  .card {
    position: absolute;
    width: 560px;
    height: 320px;
    background: var(--paper);
    box-shadow: 0 4px 14px rgba(0,0,0,.12);
    overflow: hidden;
  }
  .card-front { left: 560px; top: 50px; }
  .card-back  { left: 80px;  top: 420px; }

  .brand {
    display: flex;
    align-items: center;
    gap: 14px;
  }
  .brand-dot {
    width: 46px; height: 46px;
    border-radius: 50%;
    background: var(--teal);
    flex: none;
  }
  .brand-name {
    color: var(--teal);
    font-weight: 700;
    text-transform: uppercase;
    line-height: 1.1;
    letter-spacing: .5px;
  }

  /* Front */
  .card-front .brand {
    position: absolute;
    left: 0; right: 0; top: 104px;
    justify-content: center;
  }
  .card-front .brand-name { font-size: 26px; }
  .front-url {
    position: absolute;
    left: 0; right: 0; top: 236px;
    text-align: center;
    color: var(--teal);
    font-size: 14px;
    letter-spacing: 2.5px;
  }

  /* Back */
  .card-back .brand {
    position: absolute;
    left: 30px; top: 24px;
  }
  .card-back .brand-dot { width: 38px; height: 38px; }
  .card-back .brand-name { font-size: 20px; }

  .animal-art {
    position: absolute;
    left: 352px; top: 96px;
    width: 208px; height: 224px;
    background: linear-gradient(160deg, var(--teal) 0%, var(--teal-dark) 100%);
  }

  .person {
    position: absolute;
    left: 30px; top: 100px;
  }
  .person-name {
    color: var(--teal);
    font-weight: 700;
    font-size: 19px;
    text-transform: uppercase;
    white-space: nowrap;
  }
  .person-creds { font-size: 12px; text-transform: none; }
  .person-title { color: var(--ink); font-size: 14px; margin-top: 1px; }

  .address {
    position: absolute;
    left: 30px; top: 162px;
    color: var(--ink);
    font-size: 13px;
    line-height: 1.4;
    font-style: normal;
  }
  .contacts {
    position: absolute;
    left: 30px; top: 212px;
    list-style: none;
    color: var(--ink);
    font-size: 12.5px;
    line-height: 1.55;
  }
  .contacts li { display: flex; align-items: center; gap: 7px; white-space: nowrap; }
  .contacts svg { width: 12px; height: 12px; flex: none; }
</style>
</head>
<body>

<section class="card card-front" aria-label="Card front">
  <div class="brand">
    <span class="brand-dot"></span>
    <div class="brand-name">Ridgeline<br>Pet Vision Care</div>
  </div>
  <p class="front-url">ridgelinepetvisioncare-example.net</p>
</section>

<section class="card card-back" aria-label="Card back">
  <div class="animal-art" role="img" aria-label="Illustration area: large teal silhouettes of a horse, a dog and a cat"></div>

  <div class="brand">
    <span class="brand-dot"></span>
    <div class="brand-name">Ridgeline<br>Pet Vision Care</div>
  </div>

  <div class="person">
    <p class="person-name">Delia Vossman <span class="person-creds">BSc, DVM, MSc, DipACVO</span></p>
    <p class="person-title">Veterinary Ophthalmologist</p>
  </div>

  <address class="address">
    1874 Thornbury Rd<br>
    Kelowna, BC, V1X 4M9
  </address>

  <ul class="contacts">
    <li>
      <svg viewBox="0 0 24 24" aria-hidden="true"><path fill="var(--teal)" d="M6.6 10.8a15.1 15.1 0 0 0 6.6 6.6l2.2-2.2a1 1 0 0 1 1-.25 11.4 11.4 0 0 0 3.6.57 1 1 0 0 1 1 1V20a1 1 0 0 1-1 1A17 17 0 0 1 3 4a1 1 0 0 1 1-1h3.5a1 1 0 0 1 1 1c0 1.25.2 2.45.57 3.57a1 1 0 0 1-.25 1z"/></svg>
      250.418.3927
    </li>
    <li>
      <svg viewBox="0 0 24 24" aria-hidden="true"><rect x="2" y="5" width="20" height="14" fill="none" stroke="var(--teal)" stroke-width="2.2"/><path d="M2 5l10 8 10-8" fill="none" stroke="var(--teal)" stroke-width="2.2"/></svg>
      ridgelinepetvisioncare@mailbox-example.net
    </li>
    <li>
      <svg viewBox="0 0 24 24" aria-hidden="true"><g fill="none" stroke="var(--teal)" stroke-width="2"><circle cx="12" cy="12" r="10"/><ellipse cx="12" cy="12" rx="4.5" ry="10"/><path d="M2 12h20M4 7h16M4 17h16"/></g></svg>
      ridgelinepetvisioncare-example.net
    </li>
  </ul>
</section>

</body>
</html>
```